Kitchen and custom cabinetry company looking for business card design

We make: * Custom Kitchens, contemporary and traditional kitchens, Vanities, Libraries, Custom Entry Doors, Custom Wine Cellars and Custom Design Furniture. Phone number 555-284-7716. Address: Westhampton NY. Email: KAVRO@mailbox.example Portfolio at: KAVROcabinetry.example I would like moderns fonts and not heavy lines. double side but maybe will use clear plastic. I attached the logo.

Industry/Entity Type

Business

```html
<!DOCTYPE html>
<html lang="en">
<head>
<meta charset="utf-8">
<title>Kavro – Business Card</title>
<link rel="stylesheet" href="https://fonts.googleapis.com/css2?family=Cinzel:wght@400;700&display=swap">
<style>
  :root {
    --page-bg: #d8d3cb;
    --card-light: #e9e7e4;
    --card-light-2: #dcdad7;
    --band-dark: #3a3a3b;
    --band-dark-2: #2b2b2c;
    --accent: #d9553a;
    --brand-grey: #505052;
    --text-grey: #6a6a6a;
    --text-light: #e6e2dc;
  }
  * { margin: 0; padding: 0; box-sizing: border-box; }
  html, body {
    width: 1200px; height: 970px; overflow: hidden;
    background: var(--page-bg);
  }
  .card {
    position: absolute; left: 62px; top: 185px;
    width: 1076px; height: 600px;
    background: linear-gradient(180deg, var(--card-light), var(--card-light-2));
    box-shadow: 0 18px 40px rgba(0,0,0,0.22);
    overflow: hidden;
    font-family: "Cinzel", serif;
  }
  .name-marker {
    position: absolute; left: 0; top: 34px; width: 18px; height: 80px;
    background: var(--accent);
  }
  .holder { position: absolute; left: 44px; top: 42px; }
  .holder-name { font-weight: 700; font-size: 31px; color: var(--accent); line-height: 1.1; }
  .holder-role { font-size: 24px; color: var(--text-grey); margin-top: 4px; }

  .brand-name {
    position: absolute; right: 52px; top: 140px;
    font-weight: 700; font-size: 84px; line-height: 1;
    color: var(--brand-grey); letter-spacing: 4px;
  }
  .brand-rule {
    position: absolute; left: 661px; top: 293px; width: 376px; height: 9px;
    background: var(--accent);
  }

  .info-band {
    position: absolute; left: 0; top: 302px; width: 100%; height: 298px;
    background: linear-gradient(180deg, var(--band-dark), var(--band-dark-2));
  }
  .services {
    position: absolute; left: 30px; top: 18px; list-style: none;
    color: var(--text-light); font-size: 23px; line-height: 33px;
  }
  .services li::before {
    content: ""; display: inline-block; width: 11px; height: 11px; border-radius: 50%;
    background: var(--accent); margin-right: 14px; vertical-align: 3px;
  }
  .contacts {
    position: absolute; right: 50px; top: 108px; list-style: none;
    color: var(--text-light); font-size: 21px; line-height: 30px; text-align: right;
  }
  .contacts li { display: flex; justify-content: flex-end; align-items: center; gap: 14px; }
  .contacts svg { width: 24px; height: 20px; flex: none; }
</style>
</head>
<body>
  <div class="card">
    <div class="name-marker"></div>
    <div class="holder">
      <div class="holder-name">Dana Merrow</div>
      <div class="holder-role">Manager</div>
    </div>

    <div class="brand-name">KAVRO</div>
    <div class="brand-rule"></div>

    <div class="info-band">
      <ul class="services">
        <li>Custom Kitchens</li>
        <li>contemporary kitchens</li>
        <li>traditional kitchens</li>
        <li>Vanities</li>
        <li>Libraries</li>
        <li>Custom Entry Doors</li>
        <li>Custom Wine Cellars</li>
        <li>Custom Design Furniture.</li>
      </ul>
      <ul class="contacts">
        <li>555-284-7716
          <svg viewBox="0 0 24 20" aria-hidden="true"><path fill="var(--accent)" d="M2 7c0-3 5-5 10-5s10 2 10 5v2h-5V7c-2-1-8-1-10 0v2H2z M6 10h12l3 8H3z"/></svg>
        </li>
        <li>KAVRO@mailbox.example
          <svg viewBox="0 0 24 20" aria-hidden="true"><rect x="2" y="3" width="20" height="14" fill="var(--accent)"/><path d="M2 3l10 8 10-8" fill="none" stroke="var(--band-dark)" stroke-width="1.6"/></svg>
        </li>
        <li>KAVROcabinetry.example
          <svg viewBox="0 0 24 20" aria-hidden="true"><rect x="3" y="2" width="18" height="12" fill="none" stroke="var(--accent)" stroke-width="2"/><rect x="9" y="16" width="6" height="2" fill="var(--accent)"/></svg>
        </li>
      </ul>
    </div>
  </div>
</body>
</html>
```